Website Design Required

Our client needs a website built from scratch. The website is called Snap4Wall and is essentially a website that allows you to upload a photo, order and pay and your photo is printed onto a canvas. A closely related website is http://www.lumafold.co.za/ however this project needs a clean, fresh design that encourages purchases.

Snap4wall will be a dedicated website which allows users to upload and print a single image for large format printing.

The website flow will consist of the following:

• A landing page will be designed which showcases the product offering and offers simple and easy to understand instructions on how to get a photo up- loaded and delivered to their door.

• An upload page will exist that allows users the ability to upload a photo to the website for printing.

• Once the user has uploaded a photo the website will ensure that the dimensions are good enough for printing onto canvas and advise the user accordingly if it is not suitable.
• Once the photo has passed this validation we will take the user to a new page that will give them a preview of their photo. Here they will be given a chance to place the photo correctly should the need arise.

• Once the user is happy with the photo placement they will click on the next button which will take them to the payment and delivery page whereby they will need to complete all the fields.

• Once done, a final order page will appear confirming all the details of the order as well as payment and delivery information. Once the user is satisfied he can click the order button.

Requirements
Must have
• We will need the following pages designed:
1. Homepage
2. Upload page
3. Photo placement page (which allows users to align their photo onto the canvas)
4. Order & Payment page
Should not have
• The design should not use old style fonts and shoddy illustrations. If illustrations are used they have to be clean, simple, stylish.

```html
<!DOCTYPE html>
<html lang="en">
<head>
<meta charset="utf-8">
<title>Snap4Wall – Order &amp; Payment</title>
<link rel="stylesheet" href="https://fonts.googleapis.com/css2?family=PT+Sans:wght@400;700&display=swap">
<style>
:root{
  --backdrop:#000;
  --frame:#7a7a7a;
  --frame-edge:#fff;
  --sky:#a8d3dc;
  --panel-border:#9a9a9a;
  --text:#222;
  --muted:#999;
  --field-border:#d6d6d6;
  --row:#f1f1f1;
  --accent:#8cc63f;
  --required:#e0262b;
  --nav-top:#fbfbfb;
  --nav-bottom:#dcdcdc;
  --tab:#777;
}
*{box-sizing:border-box;margin:0;padding:0}
html,body{width:1024px;height:1200px;overflow:hidden}
body{background:#fff;font-family:"PT Sans",Arial,sans-serif;color:var(--text);position:relative}
.backdrop{position:absolute;left:0;top:0;width:1024px;height:1140px;background:var(--backdrop)}
.smoke{position:absolute;top:60px;width:90px;height:900px;background:radial-gradient(ellipse at center,rgba(160,160,160,.35),rgba(0,0,0,0) 70%)}
.smoke.left{left:0}.smoke.right{right:0}
.frame{position:absolute;left:86px;top:22px;width:850px;height:1096px;background:var(--frame);border:2px solid var(--frame-edge)}
.page{position:absolute;left:99px;top:47px;width:819px;height:1045px;background:linear-gradient(#a8d3dc 0,#c3e2e8 150px,#fff 260px,#fff 100%)}
.abs{position:absolute}
.nav{left:137px;top:71px;width:739px;height:37px;border-radius:5px;background:linear-gradient(var(--nav-top),var(--nav-bottom));border:1px solid #c8c8c8}
.nav-tab{left:145px;top:63px;width:128px;height:47px;border-radius:8px 8px 12px 12px;background:linear-gradient(#8a8a8a,#666);border:3px solid #d8d8d8;color:#fff;font-size:17px;text-align:center;line-height:48px}
.nav-item{top:79px;font-size:17px;color:#444;transform:translateX(-50%)}
.nav-sep{top:75px;width:1px;height:30px;background:#c5c5c5;border-right:1px solid #fff}
.brand{left:278px;top:47px;width:110px;height:179px;background:#fff;padding:0 5px 6px}
.brand-inner{width:100%;height:100%;background:linear-gradient(#2a2a2a,#000 50%);color:#fff;display:flex;align-items:center;justify-content:center;font-size:19px;font-weight:700}
.order-head{left:598px;top:124px}
.order-title{left:664px;top:126px;font-size:27px;font-weight:700;color:#444;line-height:1}
.order-sub{left:665px;top:154px;font-size:17px;color:#666}
.order-step{left:784px;top:124px;font-size:46px;font-weight:700;color:#444;line-height:1}
.panel{left:135px;top:187px;width:743px;height:831px;background:#fff;border:3px solid var(--panel-border);border-radius:3px}
.h2{font-size:19px;color:#222}
.qty{left:624px;top:232px;width:216px;height:70px;border:2px solid #d2d2d2}
.qty-label{left:650px;top:244px;font-size:17px}
.qty-select{left:747px;top:247px;width:38px;height:18px;border:1px solid #ccc;font-size:13px;padding-left:4px;line-height:16px}
.qty-note{left:651px;top:267px;font-size:13px}
.th,.td{font-size:13px}
.row{left:173px;top:354px;width:664px;height:26px;background:var(--row)}
.total{right:189px;top:387px;font-size:13px;font-weight:700}
.link{font-size:13px;font-weight:700;color:var(--accent)}
.label{left:180px;font-size:13px}
.label span{color:var(--required)}
.field{left:275px;width:210px;height:23px;border:2px solid var(--field-border);background:#fff}
.select{font-size:13px;color:var(--muted);padding-left:9px;line-height:19px}
.arrow{position:absolute;right:3px;top:2px;width:17px;height:15px;background:#d4d4d4}
.arrow::after{content:"";position:absolute;left:4px;top:5px;border:5px solid transparent;border-top:6px solid #555}
.visual{left:620px;top:480px;width:170px;height:222px;border-radius:4px;background:radial-gradient(circle at 50% 35%,#e8dcc8,#b8916a 45%,#f4f0ea 75%,#fff)}
.card{width:89px;height:58px;border-radius:5px;display:flex;align-items:center;justify-content:center;gap:5px;font-size:15px;font-weight:700;color:#fff}
.card i{width:10px;height:10px;background:#fff;display:block}
.card.c1{left:181px;top:834px;background:#d94040}
.card.c2{left:316px;top:834px;background:#3a7fcf}
.card.c3{left:456px;top:834px;background:#1e4a9a}
.radio{width:10px;height:10px;border-radius:50%;border:1px solid #aaa;background:radial-gradient(#777 30%,#eee 40%);top:906px}
.pay-btn{left:279px;top:934px;width:134px;height:38px;border:1px solid #ccc;border-radius:3px;background:linear-gradient(#fff,#e7e7e7);font-size:20px;display:flex;align-items:center;justify-content:center;gap:8px}
.divider{left:563px;top:820px;width:1px;height:164px;background:#ccc}
.seal{left:681px;top:821px;width:72px;height:72px;border-radius:50%;background:radial-gradient(#f3e27a,#c9a935)}
.wallet{left:660px;top:895px;width:116px;text-align:center;font-size:19px;font-weight:700;color:#1f3f8a}
.mini{height:20px;width:26px;border-radius:2px}
.foot-card{top:1038px;width:35px;height:23px;border-radius:3px;font-size:7px;font-weight:700;color:#fff;display:flex;align-items:center;justify-content:center}
.foot-links{left:0;width:1024px;top:1070px;text-align:center;font-size:9px;color:#000}
</style>
</head>
<body>
<div class="backdrop"></div>
<div class="smoke left" role="img" aria-label="Soft smoke swirls"></div>
<div class="smoke right" role="img" aria-label="Soft smoke swirls"></div>
<div class="frame"></div>
<div class="page"></div>

<nav>
  <div class="abs nav"></div>
  <div class="abs nav-tab">Home</div>
  <span class="abs nav-item" style="left:461px">Canvas Options</span>
  <span class="abs nav-sep" style="left:537px"></span>
  <span class="abs nav-item" style="left:590px">Pricing</span>
  <span class="abs nav-sep" style="left:648px"></span>
  <span class="abs nav-item" style="left:708px">Blog</span>
  <span class="abs nav-sep" style="left:765px"></span>
  <span class="abs nav-item" style="left:822px">Contact</span>
</nav>
<div class="abs brand"><div class="brand-inner">Snap4Wall</div></div>

<svg class="abs order-head" width="56" height="52" viewBox="0 0 56 52" aria-hidden="true">
  <path d="M26 4 L38 22" stroke="#555" stroke-width="3" fill="none"/>
  <rect x="1" y="18" width="54" height="8" rx="2" fill="#7cbf2a"/>
  <path d="M4 26 H52 L48 50 H8 Z" fill="#8cc63f"/>
  <g stroke="#5f9e1c" stroke-width="2"><line x1="14" y1="30" x2="15" y2="46"/><line x1="22" y1="30" x2="22" y2="46"/><line x1="30" y1="30" x2="30" y2="46"/><line x1="38" y1="30" x2="38" y2="46"/><line x1="46" y1="30" x2="45" y2="46"/></g>
</svg>
<div class="abs order-title">ORDER</div>
<div class="abs order-sub">Pay and order</div>
<div class="abs order-step">3</div>

<div class="abs panel"></div>

<h2 class="abs h2" style="left:170px;top:257px">Order Review</h2>
<div class="abs qty"></div>
<span class="abs qty-label">Quantity</span>
<div class="abs qty-select">1<span class="arrow" style="top:1px;right:1px;height:14px"></span></div>
<span class="abs qty-note">50% Off Additional Copies</span>

<span class="abs th" style="left:337px;top:334px">Canvas</span>
<span class="abs th" style="left:481px;top:334px">Frame</span>
<span class="abs th" style="left:625px;top:334px">Effect Canvas</span>
<span class="abs th" style="left:791px;top:334px">Price</span>
<div class="abs row"></div>
<span class="abs td" style="left:179px;top:359px">Canvas 1 - 11x14</span>
<span class="abs td" style="left:336px;top:359px">R48.74</span>
<span class="abs td" style="left:480px;top:359px">R0.00</span>
<span class="abs td" style="left:624px;top:359px">R0.00</span>
<span class="abs td" style="left:791px;top:359px">R48.74</span>
<span class="abs total">Your Total:&nbsp; R48.74</span>
<span class="abs link" style="right:189px;top:416px">Create another canvas</span>

<h2 class="abs h2" style="left:175px;top:466px">Shipping Info</h2>
<span class="abs label" style="top:509px">Country :<span>*</span></span>
<div class="abs field select" style="top:505px">South Africa<span class="arrow"></span></div>
<span class="abs label" style="top:539px">Email :<span>*</span></span>
<div class="abs field" style="top:535px"></div>
<span class="abs label" style="top:569px">First Name :<span>*</span></span>
<div class="abs field" style="top:565px"></div>
<span class="abs label" style="top:599px">Last Name :<span>*</span></span>
<div class="abs field" style="top:595px"></div>
<span class="abs label" style="top:629px">Address :<span>*</span></span>
<div class="abs field" style="top:625px"></div>
<span class="abs label" style="top:659px">Address 2 :<span>*</span></span>
<div class="abs field" style="top:655px"></div>
<span class="abs label" style="top:689px">City :<span>*</span></span>
<div class="abs field" style="top:685px"></div>
<span class="abs label" style="top:719px">Province :<span>*</span></span>
<div class="abs field select" style="top:715px;width:145px">Select a province<span class="arrow"></span></div>
<span class="abs label" style="left:433px;top:719px">Postal Code:<span>*</span></span>
<div class="abs field" style="left:525px;top:715px;width:108px"></div>
<span class="abs label" style="top:749px">Phone :<span>*</span></span>
<div class="abs field" style="top:745px"></div>

<div class="abs visual" role="img" aria-label="Globe with parcels and a computer mouse, representing worldwide delivery"></div>

<div class="abs card c1"><i></i>Cardora</div>
<div class="abs card c2"><i></i>Amerix</div>
<div class="abs card c3"><i></i>Vantra</div>
<span class="abs radio" style="left:216px"></span>
<span class="abs radio" style="left:356px"></span>
<span class="abs radio" style="left:496px"></span>
<div class="abs pay-btn">
  <svg width="36" height="30" viewBox="0 0 36 30" aria-hidden="true"><path d="M2 3 H8 L13 20 H30 L34 8 H10" fill="none" stroke="#222" stroke-width="3" stroke-linejoin="round"/><circle cx="15" cy="26" r="3" fill="#222"/><circle cx="28" cy="26" r="3" fill="#222"/></svg>
  Pay Now
</div>

<div class="abs divider"></div>
<div class="abs seal"></div>
<div class="abs wallet">PayNest</div>
<div class="abs mini" style="left:661px;top:920px;background:#1e4a9a"></div>
<div class="abs mini" style="left:692px;top:920px;background:#d94040"></div>
<div class="abs mini" style="left:723px;top:920px;background:#e07a1f"></div>
<div class="abs mini" style="left:753px;top:920px;background:#3a7fcf;width:21px"></div>
<span class="abs link" style="left:621px;top:956px">Continue using secure paiment</span>

<div class="abs foot-card" style="left:429px;background:#d94040">Cardora</div>
<div class="abs foot-card" style="left:473px;background:#3a7fcf">Amerix</div>
<div class="abs foot-card" style="left:515px;background:#1f3f8a">PayNest</div>
<div class="abs foot-card" style="left:557px;background:#1e4a9a">Vantra</div>
<div class="abs foot-links">Terms &amp; Conditions | Privacy Policy</div>
</body>
</html>
```